New Business Card Design Project

I need a design for business cards, i am an electrical business called "Corvane Electrical and Communications" i need the cards to be double sided with the company logo on the back (attached) the front needs to say my company name, web site, email address, telephone number, and ABN number and electrical license number. I am open to different arrangements of the information but would like the background to be incorporating something electrical or something that looks smart. open to all additional ideas also.

The company colours are orange and grey see logo attached.

Business Name: Corvane Electrical and Communications
Website: corvaneelectricalandcomms.example.com.au
Email: brent@corvaneelectricalandcomms.example.com.au
Telephone(mobile): 0481209736
ABN: 71208349162
Lic No: 418273D

Target Market(s)

Business entities, Project Managers, Accounts, Clients

Industry/Entity Type

Electrician

Contact Information for Business Card

I need a design for business cards, i am an electrical business called "Corvane Electrical and Communications" i need the cards to be double sided with the company logo on the back (attached) the front needs to say my company name

Font styles to use
Serif
Sans Serif

Colors
f37122
5c5c5c

Requirements
Must have
• Must have the Logo on the back open to different ways of it being on the back but had in mind to keep it central but again open to other options
Nice to have
• A real modern cool background that is eye catching yet contemporary
Should not have
• No backgrounds of a light bulb or plug or anything like that

```html
<!DOCTYPE html>
<html lang="en">
<head>
<meta charset="utf-8">
<title>Corvane Electrical and Communications – Business Card</title>
<link rel="stylesheet" href="https://fonts.googleapis.com/css2?family=Mulish:wght@400;600;700;800&display=swap">
<style>
  :root {
    --stage: #4b4b4d;
    --card-grey: #59595b;
    --orange: #fbae17;
    --white: #ffffff;
    --ink: #4a4a4c;
    --ink-soft: #6a6a6c;
  }
  * { box-sizing: border-box; margin: 0; padding: 0; }
  html, body {
    width: 1105px; height: 1200px; overflow: hidden;
    background: var(--stage);
    font-family: "Mulish", sans-serif;
  }
  .canvas { position: relative; width: 1105px; height: 1200px; }

  .card {
    position: absolute; left: 196px; width: 720px; height: 411px;
    border-radius: 19px; overflow: hidden;
  }
  .card--front { top: 146px; background: var(--card-grey); }
  .card--back { top: 602px; background: var(--orange); }

  .front__tab {
    position: absolute; left: 0; top: 97px; width: 14px; height: 243px;
    background: var(--orange); border-radius: 0 8px 8px 0;
  }
  .front__brand {
    position: absolute; left: 55px; top: 196px; width: 260px;
    color: var(--white); font-weight: 700; line-height: 1.05;
  }
  .front__brand-name { display: block; font-size: 46px; letter-spacing: 0.5px; }
  .front__brand-sub { display: block; font-size: 12px; letter-spacing: 0.5px; margin-top: 8px; color: var(--orange); }

  .front__panel {
    position: absolute; left: 348px; top: 95px; width: 372px; height: 246px;
    background: var(--white); border-radius: 14px 0 0 14px;
    padding: 14px 0 0 24px; color: var(--ink-soft);
  }
  .contact__name { font-size: 27px; font-weight: 700; color: var(--orange); line-height: 1.15; }
  .contact__role { font-size: 19px; font-weight: 700; color: var(--ink); margin-bottom: 14px; }
  .contact__reg { font-size: 19px; line-height: 1.45; }
  .contact__list { list-style: none; margin-top: 10px; }
  .contact__item {
    display: flex; align-items: center; gap: 8px;
    font-size: 16px; line-height: 27px; white-space: nowrap;
  }
  .contact__item--email { font-size: 13px; letter-spacing: -0.2px; }
  .contact__item--web { font-size: 14px; letter-spacing: -0.1px; }
  .contact__icon { width: 16px; height: 16px; flex: none; }

  .back__brand {
    position: absolute; left: 0; right: 0; top: 170px;
    display: flex; align-items: center; justify-content: center; gap: 16px;
    color: var(--white); font-weight: 700; font-size: 54px; letter-spacing: 2px;
  }
  .back__dot { width: 22px; height: 22px; border-radius: 50%; background: var(--white); }
  .back__web {
    position: absolute; left: 0; right: 0; top: 328px; text-align: center;
    color: var(--white); font-size: 18px; letter-spacing: 1.6px;
  }
</style>
</head>
<body>
<main class="canvas">
  <section class="card card--front" aria-label="Business card front">
    <div class="front__tab"></div>
    <div class="front__brand">
      <span class="front__brand-name">CORVANE</span>
      <span class="front__brand-sub">ELECTRICAL &amp; COMMUNICATIONS</span>
    </div>
    <div class="front__panel">
      <p class="contact__name">Dale Marsh</p>
      <p class="contact__role">CEO/Founder</p>
      <p class="contact__reg">ABN: 71208349162<br>Lic No: 418273D</p>
      <ul class="contact__list">
        <li class="contact__item">
          <svg class="contact__icon" viewBox="0 0 16 16" aria-hidden="true"><rect x="4" y="1" width="8" height="14" rx="2" fill="none" stroke="#fbae17" stroke-width="2"/></svg>
          0481209736
        </li>
        <li class="contact__item contact__item--email">
          <svg class="contact__icon" viewBox="0 0 16 16" aria-hidden="true"><rect x="1" y="3" width="14" height="10" fill="#fbae17"/><path d="M1 3l7 6 7-6" fill="none" stroke="#fff" stroke-width="1.3"/></svg>
          brent@corvaneelectricalandcomms.example.com.au
        </li>
        <li class="contact__item contact__item--web">
          <svg class="contact__icon" viewBox="0 0 16 16" aria-hidden="true"><circle cx="8" cy="8" r="7" fill="#fbae17"/><path d="M3 8h10M8 1c-3 4-3 10 0 14M8 1c3 4 3 10 0 14" fill="none" stroke="#fff" stroke-width="1"/></svg>
          corvaneelectricalandcomms.example.com.au
        </li>
      </ul>
    </div>
  </section>

  <section class="card card--back" aria-label="Business card back">
    <div class="back__brand"><span class="back__dot"></span>CORVANE</div>
    <p class="back__web">www.corvaneelectricalandcomms.example.com.au</p>
  </section>
</main>
</body>
</html>
```